Brand new redesign of Brightpath finance website

I need a new website design that i can advertise a great low interest rate on the front page and capture input application details that will send through to my email address.

some car finance companies will be similar to this would be listed below

tallowcredit.example.com.au
mirabelfinance.example.com.au
finance725.example.com.au
quenbyfinance.example.com.au
finance91.example.com.au

Reason: I have changed the project to a committed project. all the webpages should have the same format just different content and i want to be able to edit the front page easily to update my interest rates.

Target Market(s)

Australian Finance market targeting a younger demographic

Industry/Entity Type

Finance

Coding

Coded - Design and coding required

Number of Pages Required

5+ page

Font styles to use
Serif
Sans Serif

Colors
0255a3
ffffff
cedeed

Requirements
Must have
• application capture form
• apply now buttons
• Headline rate front page

```html
<!DOCTYPE html>
<html lang="en">
<head>
<meta charset="utf-8">
<title>Brightpath Finance – Home</title>
<link rel="stylesheet" href="https://fonts.googleapis.com/css2?family=Roboto:wght@400;500;700&family=Lato:wght@400;700&display=swap">
<style>
:root{
  --blue:#0255a3;
  --blue-dark:#0a3f86;
  --white:#ffffff;
  --pale:#cedeed;
  --ink:#2b2b2b;
  --grey:#6b6b6b;
  --line:#d8d8d8;
  --btn-grey:#e9ecef;
}
*{margin:0;padding:0;box-sizing:border-box}
html,body{width:793px;height:1200px;overflow:hidden;background:var(--white)}
body{position:relative;font-family:'Lato',sans-serif;color:var(--ink)}
.abs{position:absolute}

/* top bar */
.topbar{left:0;top:0;width:793px;height:29px;background:var(--blue)}
.social{top:5px;width:20px;height:20px;background:rgba(255,255,255,.35);border-radius:2px}
.apply{left:549px;top:4px;width:70px;height:21px;background:#d9dde2;color:#333;font:400 11px 'Roboto',sans-serif;line-height:21px;text-align:center}
.topphone{left:637px;top:6px;color:var(--white);font:500 13.5px 'Roboto',sans-serif;display:flex;align-items:center;gap:5px}

/* nav */
.nav{left:0;top:29px;width:793px;height:80px;background:var(--white);border-bottom:1px solid #e3e3e3}
.navlink{top:62px;font:400 11px 'Roboto',sans-serif;color:#222;letter-spacing:.2px}
.navlink.active{color:var(--blue)}
.navsep{top:61px;width:1px;height:14px;background:#cfcfcf}
.brand{left:341px;top:33px;width:112px;text-align:center}
.brand-mark{width:40px;height:40px;border-radius:50%;background:var(--blue);margin:0 auto 5px}
.brand-name{font:700 12px 'Roboto',sans-serif;color:var(--blue);letter-spacing:.5px;line-height:13px}

/* hero */
.hero{left:0;top:109px;width:793px;height:309px;background:linear-gradient(90deg,#5d6066 0%,#9a9ea4 28%,#c7c9cc 55%,#a9abae 80%,#8f9296 100%)}
.hero-points{left:358px;top:180px;list-style:none}
.hero-points li{font:400 11.5px 'Roboto',sans-serif;color:var(--blue);line-height:15px;margin-bottom:8px;padding-left:14px;position:relative}
.hero-points li::before{content:"»";position:absolute;left:0;top:0;font-size:10px}
.seal{left:431px;top:274px;width:100px;height:100px;border-radius:50%;border:2px solid rgba(255,255,255,.85)}
.arrow{top:248px}
.quote{left:552px;top:127px;width:188px;height:252px;background:rgba(206,222,237,.92)}
.quote-title{height:29px;background:var(--blue);color:var(--white);font:500 13.5px 'Roboto',sans-serif;line-height:29px;padding-left:12px}
.field{position:absolute;left:12px;width:164px;height:22px;background:var(--white);border:1px solid #dfe5eb;font:400 7.5px 'Lato',sans-serif;color:#8a8a8a;line-height:20px;padding-left:10px}
.agree{position:absolute;left:12px;top:193px;font:700 7.5px 'Lato',sans-serif;color:#444;display:flex;align-items:center;gap:8px}
.agree span.box{width:10px;height:10px;background:var(--white);border:1px solid #ccc}
.quote-btn{position:absolute;left:8px;top:217px;width:165px;height:27px;background:var(--blue);color:var(--white);font:700 12.5px 'Roboto',sans-serif;line-height:27px;text-align:center}

/* intro */
.h2{font:400 20.5px 'Roboto',sans-serif;color:#444;letter-spacing:.1px}
.h2 b{font-weight:400;color:var(--blue)}
.rule{height:1px;background:var(--line)}
.notch{width:0;height:0;border-left:5px solid transparent;border-right:5px solid transparent;border-top:5px solid var(--blue)}
.para{font:400 9.3px/15px 'Lato',sans-serif;color:#333}
.call{left:54px;top:616px;font:400 17.5px 'Roboto',sans-serif;color:#222}
.call b{font:700 23px 'Roboto',sans-serif;color:var(--blue);margin-left:8px}
.vsep{left:369px;top:470px;width:1px;height:190px;background:#e6e6e6}
.svc-icon{width:36px;height:36px;border-radius:50%;background:var(--blue);display:flex;align-items:center;justify-content:center}
.svc-title{font:500 14px 'Roboto',sans-serif;color:#222}
.svc-text{width:125px;font:400 8.3px/11.5px 'Lato',sans-serif;color:#333}

/* bands */
.band-dark{left:0;top:691px;width:793px;height:159px;background:linear-gradient(90deg,#3a3c40,#5a5c60 50%,#4a4c50)}
.band-blue{left:0;top:850px;width:793px;height:158px;background:var(--blue)}
.band-h{color:var(--white);font-family:'Roboto',sans-serif;font-weight:400}
.btn-blue{background:var(--blue);color:var(--white);font:500 16px 'Roboto',sans-serif;text-align:center}
.btn-light{background:var(--btn-grey);color:#333;font:500 16px 'Roboto',sans-serif;text-align:center}

/* footer */
.footer{left:0;top:1008px;width:793px;height:192px;background:var(--pale)}
.foot-mark{left:72px;top:1039px;width:100px;height:92px;border-radius:50%;background:#a9b0b8}
.foot-phone{left:71px;top:1150px;font:700 17px 'Roboto',sans-serif;color:var(--blue)}
.fsep{left:209px;top:1035px;width:1px;height:140px;border-left:1px dashed #b9c7d4}
.flinks{left:243px;top:1051px;font:400 12px 'Roboto',sans-serif;color:#222;display:flex;gap:14px}
.flinks i{font-style:normal;color:#444}
.ficon{width:36px;height:36px;border-radius:50%;background:var(--blue);display:flex;align-items:center;justify-content:center}
.ftext{font:400 11px/14px 'Roboto',sans-serif;color:#222;white-space:nowrap}
.ftext small{font-size:9px}
.fdiv{width:1px;height:50px;border-left:1px dashed #b9c7d4}
.dash{left:277px;top:1145px;width:440px;border-top:1px dashed #b9c7d4}
.copy{left:277px;top:1157px;width:440px;text-align:center;font:400 9.3px 'Lato',sans-serif;color:#222}
.bottom{left:0;top:1197px;width:793px;height:3px;background:var(--blue-dark)}
</style>
</head>
<body>

<!-- top bar -->
<div class="abs topbar"></div>
<span class="abs social" style="left:53px" aria-label="Social link"></span>
<span class="abs social" style="left:81px" aria-label="Social link"></span>
<span class="abs social" style="left:109px" aria-label="Social link"></span>
<div class="abs apply">APPLY NOW</div>
<div class="abs topphone">
  <svg width="11" height="11" viewBox="0 0 24 24"><path fill="#fff" d="M6.6 10.8a15 15 0 0 0 6.6 6.6l2.2-2.2c.3-.3.7-.4 1-.2 1.1.4 2.3.6 3.6.6.6 0 1 .4 1 1V20c0 .6-.4 1-1 1A17 17 0 0 1 3 4c0-.6.4-1 1-1h3.5c.6 0 1 .4 1 1 0 1.3.2 2.5.6 3.6.1.3 0 .7-.2 1z"/></svg>
  123-555-0148
</div>

<!-- navigation -->
<div class="abs nav"></div>
<span class="abs navlink active" style="left:71px">HOME</span>
<span class="abs navsep" style="left:126px"></span>
<span class="abs navlink" style="left:152px">ABOUT US</span>
<span class="abs navsep" style="left:227px"></span>
<span class="abs navlink" style="left:253px">LOANS &#8964;</span>
<div class="abs brand">
  <div class="brand-mark"></div>
  <div class="brand-name">BRIGHTPATH<br>FINANCE</div>
</div>
<span class="abs navlink" style="left:466px">INSURANCE</span>
<span class="abs navsep" style="left:532px"></span>
<span class="abs navlink" style="left:541px">FINANCE CALCULATOR</span>
<span class="abs navsep" style="left:664px"></span>
<span class="abs navlink" style="left:673px">CONTACT US</span>

<!-- hero -->
<div class="abs hero" role="img" aria-label="Smiling young woman holding car keys, sitting on the bonnet of her new car"></div>
<ul class="abs hero-points">
  <li>Low Rate Car Loans From 4.69%<br>Comparison Rate 4.99%</li>
  <li>Low Fees</li>
  <li>Low Total Cost Loans</li>
</ul>
<div class="abs seal" aria-label="Low rate guarantee seal"></div>
<svg class="abs arrow" style="left:20px" width="18" height="28" viewBox="0 0 18 28"><path d="M14 3 4 14l10 11" fill="none" stroke="#fff" stroke-width="3"/></svg>
<svg class="abs arrow" style="left:756px" width="18" height="28" viewBox="0 0 18 28"><path d="M4 3l10 11L4 25" fill="none" stroke="#fff" stroke-width="3"/></svg>

<form class="abs quote">
  <div class="quote-title">QUICK &amp; EASY QUOTE</div>
  <div class="field" style="top:38px">First Name</div>
  <div class="field" style="top:67px">Last Name</div>
  <div class="field" style="top:98px">Email Address</div>
  <div class="field" style="top:128px">Phone Number</div>
  <div class="field" style="top:159px">Loan Amount In Dollars
    <svg style="position:absolute;right:8px;top:8px" width="8" height="5" viewBox="0 0 8 5"><path d="M0 0l4 4 4-4" fill="none" stroke="#777"/></svg>
  </div>
  <div class="agree"><span class="box"></span>I Agree To The Terms &amp; Conditions</div>
  <div class="quote-btn">GET MY BEST RATE NOW</div>
</form>

<!-- intro -->
<h2 class="abs h2" style="left:54px;top:449px"><b>ONLINE LOAN</b> PRE APPROVAL</h2>
<div class="abs rule" style="left:54px;top:480px;width:288px"></div>
<div class="abs notch" style="left:81px;top:480px"></div>
<p class="abs para" style="left:54px;top:500px;width:295px">Sed ut perspiciatis unde omnis iste natus error sit voluptatem accusantium dolo remque laudantium, totam rem aperiam, eaque ipsa quae ab illo inventore veritatis et quasi architecto beatae vitae dicta sunt explicabo. Sed ut perspiciatis unde omnis iste natus error sit volu. eaque ipsa quae ab illo inventore veritatis et quasi architecto.</p>
<p class="abs para" style="left:54px;top:580px;width:295px;letter-spacing:.3px">Sed ut perspiciatis unde omnis iste natus error sit voluptatem accusantium dolo remque laudantium.</p>
<div class="abs call">Call Today <b>1300 555 042</b></div>
<div class="abs vsep"></div>

<h2 class="abs h2" style="left:393px;top:449px"><b>WE PROVIDE</b> LOANS FOR</h2>
<div class="abs rule" style="left:393px;top:480px;width:348px"></div>
<div class="abs notch" style="left:420px;top:480px"></div>

<div class="abs svc-icon" style="left:390px;top:505px"><svg width="18" height="16" viewBox="0 0 18 16"><path fill="#fff" d="M3 6l2-4h8l2 4h1v6h-2v2h-2v-2H6v2H4v-2H2V6zm2 0h8l-1-2H6zm-1 3a1 1 0 1 0 2 0 1 1 0 0 0-2 0zm8 0a1 1 0 1 0 2 0 1 1 0 0 0-2 0z"/></svg></div>
<div class="abs svc-title" style="left:437px;top:510px">VEHICLES</div>
<div class="abs svc-text" style="left:437px;top:534px">Sed ut perspiciatis unde omnis iste natus error sit volupta perspiciatis unde .</div>

<div class="abs svc-icon" style="left:575px;top:505px"><svg width="18" height="16" viewBox="0 0 18 16"><path fill="#fff" d="M6 1h6v3h3l-1 5H4L3 4h3zm1 1v2h4V2zM1 11c2 0 2 1 4 1s2-1 4-1 2 1 4 1 2-1 4-1v2c-2 0-2 1-4 1s-2-1-4-1-2 1-4 1-2-1-4-1z"/></svg></div>
<div class="abs svc-title" style="left:622px;top:510px">BOAT</div>
<div class="abs svc-text" style="left:622px;top:534px">Sed ut perspiciatis unde omnis iste natus error sit volupta perspiciatis unde .</div>

<div class="abs svc-icon" style="left:390px;top:593px"><svg width="18" height="16" viewBox="0 0 18 16"><path fill="#fff" d="M9 1l8 7h-2v7h-4v-4H7v4H3V8H1z"/></svg></div>
<div class="abs svc-title" style="left:437px;top:598px">HOME</div>
<div class="abs svc-text" style="left:437px;top:622px">Sed ut perspiciatis unde omnis iste natus error sit volupta perspiciatis unde .</div>

<div class="abs svc-icon" style="left:575px;top:593px"><svg width="16" height="18" viewBox="0 0 16 18"><circle cx="8" cy="5" r="3.5" fill="#fff"/><path fill="#fff" d="M1 17c0-5 3-7 7-7s7 2 7 7z"/></svg></div>
<div class="abs svc-title" style="left:622px;top:598px">PERSONAL</div>
<div class="abs svc-text" style="left:622px;top:622px">Sed ut perspiciatis unde omnis iste natus error sit volupta perspiciatis unde .</div>

<!-- repayments band -->
<div class="abs band-dark" role="img" aria-label="Blurred photo of a young couple talking with a finance adviser"></div>
<h3 class="abs band-h" style="left:55px;top:740px;font-size:30px">WHAT WILL MY REPAYMENTS BE?</h3>
<p class="abs band-h" style="left:55px;top:784px;font-size:15.5px">See how much you could borrow with our loan calculator.</p>
<div class="abs btn-blue" style="left:582px;top:753px;width:147px;height:35px;line-height:35px">Loan Calculator</div>

<!-- guarantee band -->
<div class="abs band-blue"></div>
<h3 class="abs band-h" style="left:54px;top:893px;font-size:23px">Find out what Guaranteed Approval Actually means</h3>
<p class="abs band-h" style="left:55px;top:929px;font-size:15.5px">See how much you could borrow with our loan calculator.</p>
<div class="abs btn-light" style="left:593px;top:906px;width:134px;height:35px;line-height:35px">Find Out More</div>

<!-- footer -->
<div class="abs footer"></div>
<div class="abs foot-mark" aria-hidden="true"></div>
<div class="abs foot-phone">1300 555 042</div>
<div class="abs fsep"></div>
<nav class="abs flinks">
  <span>Home</span><i>/</i><span>About Us</span><i>/</i><span>Loans</span><i>/</i><span>Insurance</span><i>/</i><span>Finance Calculator</span><i>/</i><span>Contact Us</span>
</nav>

<div class="abs ficon" style="left:236px;top:1088px"><svg width="12" height="16" viewBox="0 0 12 16"><path fill="#fff" d="M6 0a6 6 0 0 1 6 6c0 4-6 10-6 10S0 10 0 6a6 6 0 0 1 6-6zm0 3.5a2.5 2.5 0 1 0 0 5 2.5 2.5 0 0 0 0-5z"/></svg></div>
<div class="abs ftext" style="left:282px;top:1091px">BRIGHTPATH FINANCE<br>48 Harrow Lane<br>Fernlea QA 4100</div>
<div class="abs fdiv" style="left:405px;top:1084px"></div>
<div class="abs ficon" style="left:423px;top:1088px"><svg width="16" height="16" viewBox="0 0 24 24"><path fill="#fff" d="M6.6 10.8a15 15 0 0 0 6.6 6.6l2.2-2.2c.3-.3.7-.4 1-.2 1.1.4 2.3.6 3.6.6.6 0 1 .4 1 1V20c0 .6-.4 1-1 1A17 17 0 0 1 3 4c0-.6.4-1 1-1h3.5c.6 0 1 .4 1 1 0 1.3.2 2.5.6 3.6.1.3 0 .7-.2 1z"/></svg></div>
<div class="abs ftext" style="left:468px;top:1091px">Call Us<br>1300 555 042</div>
<div class="abs fdiv" style="left:553px;top:1084px"></div>
<div class="abs ficon" style="left:572px;top:1088px"><svg width="18" height="13" viewBox="0 0 18 13"><rect x="1" y="1" width="16" height="11" fill="none" stroke="#fff" stroke-width="1.5"/><path d="M1 1l8 6 8-6" fill="none" stroke="#fff" stroke-width="1.5"/></svg></div>
<div class="abs ftext" style="left:616px;top:1091px">Email<br><small>info@brightpathfinance.example.com</small></div>

<div class="abs dash"></div>
<div class="abs copy">Copyright © 2016 BRIGHTPATH FINANCE. All Rights Reserved.</div>
<div class="abs bottom"></div>

</body>
</html>
```